Vellisant - Quality health delivered at your door

Vellisant offers home and Community Based Services for adults who wish to continue live independently in their communities. We increase accessibility to health care, reduce health care delivery gap, reduce mortality and morbidity, reduce health while promoting healthy living in the comfort of our patients communities or homes.

We provide on site services and deliver high quality healthcare at your door. Our experienced physicians coordinate care with our certified nurse practitioners and provide chronic care management, physical therapy, rehabilitation and medications management.

Target Market(s)

Older population living in independent living facilities

Industry/Entity Type

Health Care

Contact Information for Business Card

Vellisant

Number of Pages Required

4 page

Font styles to use
Sans Serif

Colors

Designer to choose colors to be used in the design.

```html
<!DOCTYPE html>
<html lang="en">
<head>
<meta charset="utf-8">
<title>Vellisant – Quality health delivered at your door</title>
<link href="https://fonts.googleapis.com/css2?family=Lato:wght@400;700;900&display=swap" rel="stylesheet">
<style>
:root{
  --orange:#f7a11a;
  --orange-dark:#ef8f00;
  --green:#4b7400;
  --green-dark:#3f6300;
  --text:#555b60;
  --heading-grey:#5c6166;
  --band:#ededf0;
  --white:#ffffff;
}
*{margin:0;padding:0;box-sizing:border-box}
html,body{width:1200px;height:2687px;overflow:hidden;background:var(--white);font-family:"Lato",Arial,sans-serif;color:var(--text)}
.page{position:relative;width:1200px;height:2687px}
.abs{position:absolute}

/* header */
.brand{left:120px;top:14px;width:180px;text-align:center}
.brand-dot{width:70px;height:70px;border-radius:50%;background:var(--orange);border:5px solid var(--green);margin:0 auto}
.brand-name{font-weight:700;font-size:22px;letter-spacing:1px;color:var(--green-dark);margin-top:8px}
.top-btn{top:21px;height:24px;font-size:10px;font-weight:700;text-transform:uppercase;display:flex;align-items:center;justify-content:center}
.btn-home{left:868px;width:56px;background:var(--orange);color:var(--white)}
.btn-learning{left:938px;width:117px;border:1px solid #cfcfcf;color:#777}
.phone-icon{left:868px;top:80px;width:38px;height:38px;border-radius:50%;border:2px solid var(--orange);display:flex;align-items:center;justify-content:center}
.call-label{left:921px;top:71px;font-size:10px;font-weight:700;color:#333}
.call-number{left:920px;top:88px;font-size:23px;font-weight:700;color:var(--orange)}

.main-nav{left:0;top:140px;width:1200px;height:33px;background:var(--green);display:flex;justify-content:center;gap:23px;align-items:center}
.main-nav span{color:var(--white);font-size:10px;font-weight:700;text-transform:uppercase;letter-spacing:.2px}

/* hero */
.hero{left:0;top:173px;width:1200px;height:531px;
  background:
    radial-gradient(ellipse 180px 260px at 800px 330px,rgba(150,165,190,.55),rgba(150,165,190,0)),
    linear-gradient(180deg,#6f9a3c 0%,#8fb055 28%,#b9bfa6 44%,#c7c3ba 60%,#b6b1a8 100%)}
.hero-title{left:145px;top:365px;width:297px;height:162px;background:var(--orange);color:var(--white);font-size:32px;font-weight:900;line-height:41px;padding:18px 20px;text-transform:uppercase}
.dots{left:560px;top:659px;display:flex;gap:10px}
.dots i{width:8px;height:8px;border-radius:50%;background:#3c3c3c;display:block}

/* welcome */
.welcome-photo{left:133px;top:783px;width:453px;height:292px;
  background:
    radial-gradient(ellipse 120px 120px at 230px 150px,rgba(190,180,165,.5),rgba(190,180,165,0)),
    linear-gradient(180deg,#4f7a2c 0%,#7aa447 45%,#a3c46a 100%)}
.welcome-badge{left:487px;top:754px;width:125px;height:125px;border-radius:50%;background:var(--orange);border:8px solid var(--green-dark);box-shadow:0 0 0 4px var(--white)}
.welcome-title{left:646px;top:784px;font-size:23px;font-weight:900;color:var(--orange);text-transform:uppercase}
.rule{height:2px;background:var(--orange)}
.welcome-rule{left:646px;top:820px;width:116px}
.welcome-copy{left:646px;top:842px;width:416px;font-size:13px;line-height:19.5px;text-align:justify}
.welcome-copy p+p{margin-top:19px}
.btn-green{background:var(--green);color:var(--white);font-size:11px;font-weight:700;text-transform:uppercase;display:flex;align-items:center;justify-content:center}
.btn-read{left:646px;top:1044px;width:119px;height:34px}

/* services */
.services{left:0;top:1143px;width:1200px;height:704px;background:var(--band)}
.services-title{left:0;top:1192px;width:1200px;text-align:center;font-size:24px;font-weight:900;color:var(--orange);text-transform:uppercase}
.services-rule{left:580px;top:1235px;width:40px}
.service-card{width:300px;height:202px}
.service-card .label{position:absolute;left:0;bottom:0;width:100%;height:32px;background:rgba(247,161,26,.92);color:var(--white);font-size:16px;font-weight:700;padding:6px 10px}
.btn-all{left:518px;top:1764px;width:166px;height:36px}

/* call to action */
.cta{left:0;top:1847px;width:1200px;height:469px;
  background:
    radial-gradient(ellipse 220px 200px at 820px 230px,rgba(235,215,200,.85),rgba(235,215,200,0)),
    radial-gradient(ellipse 260px 120px at 850px 400px,rgba(160,215,215,.8),rgba(160,215,215,0)),
    linear-gradient(90deg,#e9eef1 0%,#dfe6ea 40%,#d4dcdf 62%,#e4e6e4 100%)}
.cta-text{left:145px;top:1955px;width:460px;font-size:27px;line-height:36px;font-weight:700;color:var(--heading-grey)}
.btn-contact{left:149px;top:2092px;width:152px;height:41px;background:var(--orange);color:var(--white);font-size:14px;font-weight:700;text-transform:uppercase;display:flex;align-items:center;justify-content:center}

/* footer */
.footer{left:0;top:2316px;width:1200px;height:371px;background:var(--green)}
.footer-dot{left:550px;top:2272px;width:100px;height:100px;border-radius:50%;background:var(--orange);border:7px solid var(--green-dark);box-shadow:0 0 0 4px var(--white)}
.footer-name{left:0;top:2386px;width:1200px;text-align:center;font-size:25px;line-height:30px;font-weight:700;letter-spacing:1px;color:#1e2a10}
.follow{left:0;top:2439px;width:1200px;display:flex;justify-content:center;align-items:center;gap:12px;color:var(--white);font-size:11px;letter-spacing:3px;text-transform:uppercase}
.follow b{width:30px;height:1px;background:rgba(255,255,255,.6);display:block}
.social{left:517px;top:2477px;display:flex;gap:17px}
.social i{width:28px;height:28px;border-radius:50%;background:var(--orange);display:block}
.footer-links{left:0;top:2542px;width:1200px;text-align:center;color:var(--white);font-size:11.5px;line-height:24px}
.copyright{left:0;top:2628px;width:1200px;text-align:center;color:var(--white);font-size:11px}
</style>
</head>
<body>
<div class="page">

  <header>
    <div class="abs brand">
      <div class="brand-dot"></div>
      <div class="brand-name">VELLISANT</div>
    </div>
    <div class="abs top-btn btn-home">Home</div>
    <div class="abs top-btn btn-learning">Kaleno Learning®</div>
    <div class="abs phone-icon">
      <svg width="18" height="18" viewBox="0 0 24 24"><path d="M6.6 10.8a15.1 15.1 0 0 0 6.6 6.6l2.2-2.2a1 1 0 0 1 1-.25 11.4 11.4 0 0 0 3.6.57 1 1 0 0 1 1 1V20a1 1 0 0 1-1 1A17 17 0 0 1 3 4a1 1 0 0 1 1-1h3.5a1 1 0 0 1 1 1c0 1.25.2 2.45.57 3.57a1 1 0 0 1-.25 1z" fill="#f7a11a"/></svg>
    </div>
    <div class="abs call-label">CALL US NOW</div>
    <div class="abs call-number">555.014.2290</div>
    <nav class="abs main-nav">
      <span>Assisted Living</span><span>Skilled Nursing</span><span>Independent Living</span>
      <span>Home and Community Based Services</span><span>Respite Care</span>
      <span>Rehabilitation</span><span>Kaleno Learning Center</span>
    </nav>
  </header>

  <section>
    <div class="abs hero" role="img" aria-label="Smiling senior couple outdoors, man in a wheelchair embraced by his wife"></div>
    <h1 class="abs hero-title">High quality healthcare at your door</h1>
    <div class="abs dots"><i></i><i></i><i></i><i></i></div>
  </section>

  <section>
    <div class="abs welcome-photo" role="img" aria-label="Caregiver helping a senior man in a wheelchair in a park"></div>
    <div class="abs welcome-badge"></div>
    <h2 class="abs welcome-title">Welcome to our site</h2>
    <div class="abs rule welcome-rule"></div>
    <div class="abs welcome-copy">
      <p>Vellisant offers home and Community Based Services for adults who wish to continue to live independently in the comfort of their communities.</p>
      <p>We provide on site services and deliver high quality healthcare at your door. Our experienced physicians coordinate care with our certified nurse practitioners and provide chronic care management, physical therapy, rehabilitation and medications management.</p>
    </div>
    <div class="abs btn-green btn-read">Read More</div>
  </section>

  <section>
    <div class="abs services"></div>
    <h2 class="abs services-title">Our Services</h2>
    <div class="abs rule services-rule"></div>

    <div class="abs service-card" style="left:133px;top:1290px;background:linear-gradient(120deg,#8a6a55 0%,#b89078 45%,#6f8f6a 100%)" role="img" aria-label="Caregiver with a senior woman">
      <div class="label">Social services assessment</div></div>
    <div class="abs service-card" style="left:450px;top:1290px;background:linear-gradient(120deg,#cfc4b6 0%,#e9e2d8 50%,#8a6f5c 100%)" role="img" aria-label="Home health aide with a senior woman">
      <div class="label">Home health assistance</div></div>
    <div class="abs service-card" style="left:770px;top:1290px;background:linear-gradient(120deg,#d8e3ea 0%,#e8c9c0 50%,#8fb0cf 100%)" role="img" aria-label="Therapist exercising with a senior woman">
      <div class="label">Physical therapy</div></div>

    <div class="abs service-card" style="left:133px;top:1512px;background:linear-gradient(120deg,#e3e4e2 0%,#b7b6b0 50%,#e6ddc8 100%)" role="img" aria-label="Counsellor speaking with a patient">
      <div class="label">Mental health</div></div>
    <div class="abs service-card" style="left:450px;top:1512px;background:linear-gradient(120deg,#d9d2c6 0%,#c9a88a 50%,#ecebe6 100%)" role="img" aria-label="Dentist in a clinic">
      <div class="label">Dental health</div></div>
    <div class="abs service-card" style="left:770px;top:1512px;background:linear-gradient(120deg,#dfe2e4 0%,#4d6f93 50%,#d9c3b4 100%)" role="img" aria-label="Nurse visiting a patient at home">
      <div class="label">Skilled nursing visits</div></div>

    <div class="abs btn-green btn-all">View All Services</div>
  </section>

  <section>
    <div class="abs cta" role="img" aria-label="Smiling senior woman in a light blue cardigan"></div>
    <p class="abs cta-text">Our experienced physicians coordinate care with our certified nurse practitioners</p>
    <div class="abs btn-contact">Contact Us</div>
  </section>

  <footer>
    <div class="abs footer"></div>
    <div class="abs footer-dot"></div>
    <div class="abs footer-name">VELLISANT</div>
    <div class="abs follow"><b></b>Follow Us<b></b></div>
    <div class="abs social"><i></i><i></i><i></i><i></i></div>
    <div class="abs footer-links">
      Assisted Living &nbsp;|&nbsp; Skilled Nursing &nbsp;|&nbsp; Independent Living &nbsp;|&nbsp; Home and Community Based Services &nbsp;|&nbsp; Respite Care<br>
      Rehabilitation &nbsp;|&nbsp; Kaleno Learning Center &nbsp;|&nbsp; Kaleno Learning®
    </div>
    <div class="abs copyright">Copyrights @ 2017 All Rights Reserved</div>
  </footer>

</div>
</body>
</html>
```